Mindfulness School for Children -- Business Cards

We're looking for business cards for our school directors and owners. We're a mindfulness school for children called little lanterns. Attached are our logos/icons.

```html
<!DOCTYPE html>
<html lang="en">
<head>
<meta charset="utf-8">
<title>little lanterns — business cards</title>
<link href="https://fonts.googleapis.com/css2?family=Karla:wght@400;500;700&display=swap" rel="stylesheet">
<style>
  :root {
    --backdrop: #7b7b7b;
    --card-light: #ffffff;
    --card-dark: #313131;
    --teal: #45a9bc;
    --sage: #6dbfa6;
    --ink: #4a4a4a;
  }
  * { margin: 0; padding: 0; box-sizing: border-box; }
  html, body {
    width: 1133px;
    height: 1200px;
    overflow: hidden;
    background: var(--backdrop);
    font-family: "Karla", sans-serif;
  }
  .card {
    position: absolute;
    border-radius: 26px;
    overflow: hidden;
  }
  .card-front {
    left: 205px; top: 147px;
    width: 722px; height: 411px;
    background: var(--card-light);
  }
  .brand-panel {
    position: absolute;
    left: 310px; top: 0;
    width: 440px; height: 411px;
    background: var(--teal);
    border-radius: 206px 0 0 206px;
  }
  .brand-panel .brand-name {
    position: absolute;
    left: 0; right: 28px;
    top: 183px;
    text-align: center;
    color: var(--card-light);
    font-size: 36px;
    font-weight: 700;
    letter-spacing: 0.5px;
  }
  .holder {
    position: absolute;
    left: 35px; top: 83px;
  }
  .holder-name {
    color: var(--teal);
    font-size: 21px;
    font-weight: 700;
    letter-spacing: 1px;
    line-height: 1.1;
  }
  .holder-role {
    color: var(--sage);
    font-size: 15px;
    font-weight: 500;
    letter-spacing: 0.5px;
  }
  .contacts {
    position: absolute;
    left: 32px; top: 146px;
    list-style: none;
  }
  .contact {
    display: flex;
    align-items: center;
    gap: 7px;
    margin-bottom: 23px;
    color: var(--ink);
    font-size: 15px;
    line-height: 20px;
    letter-spacing: 0.3px;
  }
  .contact-icon {
    width: 28px; height: 28px;
    flex: none;
    border-radius: 50%;
    background: var(--teal);
    display: flex; align-items: center; justify-content: center;
  }
  .card-back {
    left: 193px; top: 635px;
    width: 728px; height: 416px;
    background: var(--card-dark);
  }
  .back-wordmark {
    position: absolute;
    left: 0; right: 0;
    top: 178px;
    text-align: center;
    color: var(--teal);
    font-size: 58px;
    font-weight: 500;
    letter-spacing: 0.5px;
  }
</style>
</head>
<body>

<section class="card card-front">
  <div class="holder">
    <p class="holder-name">NORA ELLISON</p>
    <p class="holder-role">President</p>
  </div>

  <ul class="contacts">
    <li class="contact">
      <span class="contact-icon">
        <svg width="14" height="16" viewBox="0 0 14 16"><path d="M7 1a5 5 0 0 0-5 5c0 3.6 5 9 5 9s5-5.4 5-9a5 5 0 0 0-5-5z" fill="#fff"/><circle cx="7" cy="6" r="1.9" fill="#45a9bc"/></svg>
      </span>
      <span>2140 Willow Bend Road<br>Juneau, Alaska 99801</span>
    </li>
    <li class="contact">
      <span class="contact-icon">
        <svg width="14" height="14" viewBox="0 0 24 24"><path d="M6.6 10.8a15 15 0 0 0 6.6 6.6l2.2-2.2a1 1 0 0 1 1-.25 11.4 11.4 0 0 0 3.6.6 1 1 0 0 1 1 1V20a1 1 0 0 1-1 1A17 17 0 0 1 3 4a1 1 0 0 1 1-1h3.5a1 1 0 0 1 1 1c0 1.25.2 2.45.6 3.6a1 1 0 0 1-.25 1z" fill="#fff"/></svg>
      </span>
      <span>555-214-7730<br>555-618-2049</span>
    </li>
    <li class="contact">
      <span class="contact-icon">
        <svg width="15" height="15" viewBox="0 0 16 16"><circle cx="8" cy="8" r="6.5" fill="none" stroke="#fff" stroke-width="1.8"/><path d="M8 1.5v13M1.5 8h13" stroke="#fff" stroke-width="1.4"/></svg>
      </span>
      <span>hello@littlelanterns.com<br>www.littlelanterns.com</span>
    </li>
  </ul>

  <div class="brand-panel">
    <p class="brand-name">little lanterns</p>
  </div>
</section>

<section class="card card-back">
  <p class="back-wordmark">little lanterns</p>
</section>

</body>
</html>
```